hotel's Website

Hotels website redesign for reference pictures, logo etc see http://restwellharbour.co.uk/

1. 2-3 Special offers on the main page.
2. Booking calender
3. Location Map
4. Picture gallery.
5. Journeymarks reviews.
6. short description
7. Social Media sharing.
8 Phone number and address.

Industry/Entity Type

Hotel

Requirements
Must have
• 1. 2-3 Special offers on the main page.
2. Booking calender
3. Location Map
4. Picture gallery.
5. Journeymarks reviews.
6. short description
7. Social Media sharing.

```html
<!DOCTYPE html>
<html lang="en">
<head>
<meta charset="utf-8">
<title>Restwell Harbour Inn</title>
<link rel="stylesheet" href="https://fonts.googleapis.com/css2?family=Arimo:wght@400;700&family=Crimson+Pro:wght@400;600;700&family=PT+Sans:wght@400;700&display=swap">
<style>
:root{
  --blue:#0b6cb8;
  --orange:#ef8a22;
  --red:#d8262b;
  --paper:#ece5d5;
  --paper-light:#f1ecdf;
  --text:#6b6458;
  --dark:#333;
  --darker:#262626;
  --white:#fff;
}
*{box-sizing:border-box;margin:0;padding:0}
html,body{width:1033px;height:1200px;overflow:hidden}
body{background:var(--paper);font-family:"PT Sans",sans-serif;color:var(--text);position:relative;font-size:10px}
.abs{position:absolute}
.header-band{left:0;top:0;width:1033px;height:190px;background:var(--paper-light);border-bottom:1px solid #fff}
.call{left:121px;top:22px;display:flex;gap:8px;align-items:flex-start}
.call-icon{width:29px;height:26px;background:#3b8fc7;border-radius:4px;margin-top:5px;display:flex;align-items:center;justify-content:center}
.call p{font-family:Arimo,sans-serif;font-weight:700;color:#444;font-size:14px;line-height:19px}
.call p span{display:block;color:#555;font-size:13px}
.call p strong{color:#222;font-size:14px}
.brand{left:437px;top:0;width:159px;height:133px;background:#fff;box-shadow:0 1px 4px rgba(0,0,0,.2);text-align:center;border-bottom:4px solid var(--orange)}
.brand::after{content:"";position:absolute;left:0;right:0;bottom:-7px;height:3px;background:var(--red)}
.brand-name{margin-top:34px;font-family:"PT Sans",sans-serif;font-weight:700;font-size:17px;line-height:20px;color:var(--blue)}
.brand-sub{margin-top:22px;font-family:Arimo,sans-serif;font-weight:700;font-size:9px;letter-spacing:2.4px;color:#222}
.social{left:744px;top:10px;display:flex;gap:6px}
.social span{width:29px;height:29px;border-radius:50%;background:#fff;box-shadow:0 1px 2px rgba(0,0,0,.2)}
.translate{left:773px;top:52px;width:139px;height:25px;background:#f7f7f5;border:1px solid #d2cdc2;font-family:Arimo,sans-serif;font-size:10px;color:#333;display:flex;align-items:center;padding-left:6px;gap:6px}
.translate i{display:inline-block;width:15px;height:10px}
.nav{left:121px;top:87px;width:791px;height:36px;background:var(--blue);font-family:Arimo,sans-serif;font-weight:700;font-size:11.5px;color:#fff}
.nav a{position:absolute;color:#fff;text-decoration:none;top:10px}
.nav .active{background:var(--orange);padding:4px 8px;border-radius:2px;top:5px}
.hero{left:121px;top:123px;width:791px;height:346px;background:linear-gradient(120deg,#d9b48a 0%,#b27a4c 40%,#8a5331 70%,#c89a6a 100%)}
.slogan{left:139px;top:255px;width:248px;height:65px;background:rgba(241,234,220,.85);font-family:"Crimson Pro",serif;font-size:24px;line-height:24px;color:#3a3530;padding:9px 8px}
.dots{left:134px;top:448px;display:flex;gap:6px}
.dots span{width:11px;height:11px;border-radius:50%;background:#f2f0ea}
.dots span:first-child{background:var(--orange)}
.booking{left:653px;top:163px;width:251px;height:248px;background:#fff;border-radius:5px;padding:0 12px}
.booking h2{font-family:"Crimson Pro",serif;font-weight:700;color:var(--blue);font-size:20px;text-align:center;padding:22px 0 8px;border-bottom:1px solid #e3e0da;letter-spacing:.5px}
.field{position:absolute;height:24px;border:1px solid #d2d0cc;font-family:Arimo,sans-serif;font-size:10px;color:var(--blue);padding:6px 5px;background:#fff}
.field b{position:absolute;right:3px;top:3px;width:16px;height:16px;background:#8a8a8a;border-radius:2px}
.field.select b{background:#7da7d8}
.btn{background:var(--blue);color:#fff;font-family:"Crimson Pro",serif;font-weight:700;font-size:12.5px;letter-spacing:.5px;padding:4px 6px;display:inline-block}
.sec-title{font-family:"Crimson Pro",serif;font-weight:400;font-size:23px;color:var(--blue);display:flex;align-items:center;gap:10px;white-space:nowrap;letter-spacing:-.3px}
.sec-title em{font-style:normal;color:var(--orange)}
.sec-title::after{content:"";flex:1;height:3px;border-top:1px solid #eab37a;border-bottom:1px solid #eab37a}
.dot-mark{width:22px;height:22px;border-radius:50%;background:var(--orange)}
.photo{background:linear-gradient(135deg,#9a8a78,#5b4a3c);border:6px solid #d9cfbd}
.body{font-size:10px;line-height:15.7px;color:var(--text)}
.more{font-family:"Crimson Pro",serif;font-size:10px;color:var(--red);display:flex;align-items:center;gap:5px}
.more::before{content:"";width:9px;height:9px;border-radius:50%;background:var(--orange)}
.offer-title{font-family:"Crimson Pro",serif;font-weight:700;color:var(--blue);font-size:12px}
.gallery{left:121px;top:750px;width:520px;height:157px;background:linear-gradient(#f0f0ee,#fbfbfa);border-radius:4px}
.thumb{position:absolute;top:57px;width:139px;height:81px;background:#fff;border:1px solid #ddd;padding:5px}
.thumb div{width:100%;height:100%}
.arrow{position:absolute;top:90px;width:16px;height:16px;border-radius:50%;background:#d6d6d4}
.contact-line{left:661px;display:flex;align-items:center;gap:8px;font-size:9.5px;color:#333}
.footer{left:0;top:952px;width:1033px;height:248px;background:var(--dark);border-top:3px solid var(--orange)}
.footnav{left:0;top:963px;width:1033px;text-align:center;font-family:"Crimson Pro",serif;font-size:12px;color:#d8d8d8;padding-bottom:8px;border-bottom:1px solid #3e3e3e}
.footnav span{display:inline-block;width:5px;height:5px;border-radius:50%;background:var(--orange);margin:0 8px 2px}
.fcol h3{font-family:"Crimson Pro",serif;font-weight:400;font-size:16px;color:#fff;display:flex;align-items:center;gap:10px}
.fcol h3::after{content:"";flex:1;height:3px;border-top:1px solid #666;border-bottom:1px solid #666}
.fcol p,.fcol li{font-size:9.5px;line-height:13px;color:#fff}
.fcol ul{list-style:none;margin-top:12px}
.fcol li::before{content:"» ";color:#aaa}
.vline{position:absolute;top:1015px;width:1px;height:135px;background:#444}
.bottom{left:0;top:1169px;width:1033px;height:31px;background:var(--darker);color:#fff;font-size:10px;text-align:right;padding:8px 122px 0 0}
</style>
</head>
<body>
<div class="abs header-band"></div>

<div class="abs call">
  <div class="call-icon"><svg width="16" height="16" viewBox="0 0 24 24"><path fill="#fff" d="M6.6 10.8a15 15 0 0 0 6.6 6.6l2.2-2.2c.3-.3.7-.4 1-.2 1.1.4 2.3.6 3.6.6.6 0 1 .4 1 1V20c0 .6-.4 1-1 1A17 17 0 0 1 3 4c0-.6.4-1 1-1h3.5c.6 0 1 .4 1 1 0 1.3.2 2.5.6 3.6.1.3 0 .7-.2 1z"/></svg></div>
  <p><span>Call Now</span><strong>+ 44 (0) 20 7946 0182</strong></p>
</div>

<div class="abs brand">
  <div class="brand-name">Restwell<br>Harbour Inn</div>
  <div class="brand-sub">BY HARBOURLINE</div>
</div>

<div class="abs social"><span></span><span></span><span></span><span></span><span></span></div>
<div class="abs translate">TRANSLATE ▼ <i style="background:#2a4fa8"></i><i style="background:#c8202f"></i></div>

<nav class="abs nav">
  <a class="active" style="left:12px">Home</a>
  <a style="left:65px">Our Rooms</a>
  <a style="left:141px">Attractions</a>
  <a style="left:218px">London Events</a>
  <a style="left:490px;top:13px">Special Offers</a>
  <a style="left:588px;top:13px">Photos</a>
  <a style="left:647px;top:13px">Directions</a>
  <a style="left:724px;top:13px">Contact</a>
</nav>

<div class="abs hero" role="img" aria-label="Hotel breakfast room with wooden tables and chairs"></div>
<div class="abs slogan">Friendly hospitality &amp;<br>service with a smile</div>
<div class="abs dots"><span></span><span></span><span></span><span></span></div>

<form class="abs booking">
  <h2>BOOK A ROOM</h2>
  <div class="field" style="left:12px;top:71px;width:102px">Check in<b></b></div>
  <div class="field" style="left:136px;top:71px;width:102px">Check out<b></b></div>
  <div class="field select" style="left:12px;top:114px;width:226px">Select room type<b></b></div>
  <div class="field select" style="left:12px;top:157px;width:226px">No. of rooms<b></b></div>
  <div class="btn" style="position:absolute;left:12px;top:202px">SUBMIT</div>
</form>

<h2 class="abs sec-title" style="left:121px;top:490px;width:519px"><span class="dot-mark"></span><span>Welcome to <em>Restwell Harbour Inn</em></span></h2>
<div class="abs photo" style="left:121px;top:527px;width:201px;height:111px" role="img" aria-label="Hotel street frontage"></div>
<p class="abs body" style="left:337px;top:527px;width:303px">Lorem ipsum dolor sit amet, consectetuer adipiscing elit, se diam nonummy nibh euismod tincidunt ut laoreet dolore mag aliquam erat volutpat. Ut wisi enim ad minim veniam, quis nostrud exerci tation ullamcorper suscipit lobortis nisl ut aliquip ex ea commodo consequat. Duis autem vel eum iriure dolor in hendrerit vulputate velit esse molestie consequat, vel illum dolore eu feugiat n facilisis at vero eros et accumsan et iusto odio dignissim qui blan praesent</p>
<p class="abs body" style="left:123px;top:645px;width:517px">Lorem ipsum dolor sit amet, consectetuer adipiscing elit, sed diam nonummy nibh euismod tincidunt ut laoreet dolore magna aliquam erat volutpat. Ut wisi enim ad minim veniam, quis nostrud exerci tation ullamcorper suscipit lobort nisl ut aliquip ex ea commodo consequat.</p>
<div class="abs more" style="left:570px;top:703px">READ MORE</div>

<h2 class="abs sec-title" style="left:661px;top:493px;width:250px"><span>Special <em>Offers</em></span></h2>
<div class="abs photo" style="left:661px;top:535px;width:112px;height:78px;border-width:4px" role="img" aria-label="City skyline at night"></div>
<div class="abs" style="left:781px;top:533px;width:130px">
  <div class="offer-title">Explore london</div>
  <p class="body" style="margin-top:3px">London is one of the culture capitals of the world and is brimming with exciting</p>
</div>
<div class="abs more" style="left:840px;top:603px">READ MORE</div>
<div class="abs photo" style="left:661px;top:634px;width:112px;height:79px;border-width:4px" role="img" aria-label="Guest room with double bed"></div>
<div class="abs" style="left:781px;top:632px;width:130px">
  <div class="offer-title">Stay in Comfort</div>
  <p class="body" style="margin-top:3px">If you're looking for a hotel near many of London's most popular</p>
</div>
<div class="abs more" style="left:840px;top:702px">READ MORE</div>

<section class="abs gallery">
  <h2 class="sec-title" style="position:absolute;left:10px;top:17px;width:497px"><span>Picture <em>gallery</em></span></h2>
  <span class="arrow" style="left:5px"></span>
  <div class="thumb" style="left:36px"><div role="img" aria-label="Lounge with bright armchairs" style="background:linear-gradient(135deg,#6d5a4a,#d9b24a)"></div></div>
  <div class="thumb" style="left:190px"><div role="img" aria-label="Breakfast tray on a bed" style="background:linear-gradient(135deg,#e8dccb,#c9874a)"></div></div>
  <div class="thumb" style="left:343px"><div role="img" aria-label="Twin room with red throws" style="background:linear-gradient(135deg,#b4924f,#6e2a24)"></div></div>
  <span class="arrow" style="left:497px"></span>
</section>

<h2 class="abs sec-title" style="left:661px;top:743px;width:250px"><span>Location <em>Map</em></span></h2>
<div class="abs" style="left:661px;top:776px;width:250px;height:78px;border:4px solid #d9cfbd;background:linear-gradient(135deg,#e6e3dc,#d8d4ca 60%,#eedc8a)" role="img" aria-label="Street map around Victoria station"></div>
<div class="abs contact-line" style="top:864px"><svg width="12" height="16" viewBox="0 0 12 16"><path fill="#555" d="M6 0a6 6 0 0 0-6 6c0 4.5 6 10 6 10s6-5.5 6-10a6 6 0 0 0-6-6zm0 8.5A2.5 2.5 0 1 1 6 3.5a2.5 2.5 0 0 1 0 5z"/></svg>12-16 Quayside Row, Victoria London SW1V 4ZZ</div>
<div class="abs contact-line" style="top:892px"><svg width="16" height="10"><rect width="16" height="10" fill="#555"/><path d="M0 0l8 6 8-6" stroke="#ece5d5" fill="none"/></svg>stay@restwellharbour.co.uk</div>
<div class="abs contact-line" style="top:916px;gap:2px"><svg width="12" height="12" viewBox="0 0 24 24"><path fill="#555" d="M6.6 10.8a15 15 0 0 0 6.6 6.6l2.2-2.2c.3-.3.7-.4 1-.2 1.1.4 2.3.6 3.6.6.6 0 1 .4 1 1V20c0 .6-.4 1-1 1A17 17 0 0 1 3 4c0-.6.4-1 1-1h3.5c.6 0 1 .4 1 1 0 1.3.2 2.5.6 3.6.1.3 0 .7-.2 1z"/></svg>+ 44 (0) 20 7946 0182</div>
<div class="abs contact-line" style="left:800px;top:916px;gap:4px"><svg width="14" height="12"><rect y="4" width="14" height="6" fill="#555"/><rect x="3" width="8" height="4" fill="#777"/><rect x="3" y="8" width="8" height="4" fill="#999"/></svg>+ 44 (0) 20 7946 0537</div>

<footer class="abs footer"></footer>
<div class="abs footnav">Home<span></span>Our Rooms<span></span>Attractions<span></span>London Events<span></span>Special Offers<span></span>Photos<span></span>Directions<span></span>Contact</div>

<div class="abs fcol" style="left:122px;top:1001px;width:232px">
  <h3>Partner Hotels</h3>
  <p style="margin-top:10px">This hotel is owned and operated by the Quadrant Hotel Group, please take a look of some of our other hotels below:</p>
  <ul>
    <li>Larkspur Inn London - Camden Lock</li>
    <li>Larkspur Express - Earls Court</li>
    <li>Meridale House Hotel</li>
    <li>Nestly Victoria</li>
    <li>Nestly Paddington</li>
    <li>Restwell Suites - King's Cross</li>
  </ul>
</div>
<span class="vline" style="left:371px"></span>
<div class="abs fcol" style="left:394px;top:1001px;width:247px">
  <h3>Stay in Touch</h3>
  <p style="margin-top:10px">Sign up for our newsletter for latest news from Restwell Harbour Inn - Victoria</p>
  <div style="margin-top:11px;width:247px;height:24px;background:#fff;color:#333;font-size:9.5px;padding:6px 8px">Email Address</div>
  <div class="btn" style="margin-top:15px">SUBMIT</div>
</div>
<span class="vline" style="left:662px"></span>
<div class="abs fcol" style="left:679px;top:1001px;width:232px">
  <h3>Journeymarks Reviews</h3>
  <div style="margin-top:22px;display:flex;align-items:center;gap:8px;font-family:'PT Sans',sans-serif;font-size:27px;color:#fff;padding-left:10px"><span style="width:26px;height:26px;border-radius:50%;background:#fff"></span>journeymarks</div>
  <p style="margin-top:16px;color:#bbb;line-height:16px;padding-left:2px">Lorem ipsum dolor sit amet, consectetuer adipiscing elit, se diam nonummy nibh euismod...</p>
  <p style="margin-top:9px;text-align:right;font-family:'Crimson Pro',serif;font-size:10px">READ MORE</p>
</div>

<div class="abs bottom">Copyright © 2013 Restwellharbour. All Rights Reserved</div>
</body>
</html>
```